Business Card Design for a new Senior Concierge Business 1.3.24

I need a professional business card to handout at networking events for my senior helper business. I would like to use the logo I have uploaded. The design should be clear and easy to read and should list the following information...
Delia Parkhurst
Owner
www.HarborlightElderAides.com
Alder Springs, Texas
936.482.5079
Delia@harborlightelderaides.com

Target Market(s)

Senior Citizens

Industry/Entity Type

Personal Helper/ Assisstant

Contact Information for Business Card

I have included the details in the project description box.

Font styles to use
Serif

Colors
0054AA
0677BA
7BADD7
CADEEF
E8F1F8
59FF00
82FF00
B8FF75
E3FFCB
F4FFEA
E54698
E96AAD
F1A4CE
F9D9EA
FCEFF6
6B429C
8869AF
B7A5CE
E3DAEB
F3F0F8

Requirements
Must have
• Include uploaded logo
Nice to have
• The log that has been uploaded
Should not have
• No crazy fonts

```html
<!DOCTYPE html>
<html lang="en">
<head>
<meta charset="utf-8">
<title>Harborlight Elder Aides – Business Card</title>
<link rel="stylesheet" href="https://fonts.googleapis.com/css2?family=Anton&family=Lato:wght@400&family=Questrial&display=swap">
<style>
  :root {
    --purple: #6233e6;
    --pink: #d81e5b;
    --white: #ffffff;
    --ink: #1d1d1f;
    --rule: #9a9a9a;
    --stage-light: #626262;
    --stage-dark: #111111;
  }
  * { box-sizing: border-box; margin: 0; padding: 0; }
  html, body { width: 1047px; height: 1200px; overflow: hidden; }
  body {
    background: radial-gradient(ellipse 60% 55% at 50% 48%, var(--stage-light), var(--stage-dark));
    position: relative;
    font-family: "Lato", sans-serif;
  }
  .card {
    position: absolute;
    left: 156px;
    width: 743px;
    height: 423px;
    border-radius: 24px;
    box-shadow: 0 6px 18px rgba(0,0,0,0.45);
    overflow: hidden;
  }
  .card--front { top: 120px; background: var(--white); }
  .card--back { top: 634px; background: var(--pink); }

  .brand {
    position: absolute;
    top: 82px;
    left: 0; right: 0;
    display: flex;
    justify-content: center;
    align-items: center;
    gap: 18px;
  }
  .brand__dot {
    width: 58px; height: 58px;
    border-radius: 50%;
    background: var(--pink);
    flex: none;
  }
  .brand__name {
    font-family: "Questrial", sans-serif;
    color: var(--purple);
    line-height: 1;
  }
  .brand__name .line1 { display: block; font-size: 60px; }
  .brand__name .line2 { display: block; font-size: 33px; margin-top: 4px; margin-left: 4px; }

  .person {
    position: absolute;
    right: calc(743px - 329px);
    top: 298px;
    text-align: right;
  }
  .person__name {
    font-family: "Anton", sans-serif;
    font-size: 39px;
    letter-spacing: 1px;
    color: var(--purple);
    line-height: 1.05;
    white-space: nowrap;
  }
  .person__role {
    font-family: "Questrial", sans-serif;
    font-size: 19px;
    color: var(--pink);
    margin-top: -2px;
  }
  .divider {
    position: absolute;
    left: 352px;
    top: 278px;
    width: 1px;
    height: 98px;
    background: var(--rule);
  }
  .contacts {
    position: absolute;
    left: 376px;
    top: 275px;
    list-style: none;
  }
  .contacts li {
    display: flex;
    align-items: center;
    gap: 11px;
    height: 25.5px;
    font-size: 17.5px;
    color: var(--ink);
    letter-spacing: 0.2px;
    white-space: nowrap;
  }
  .contacts li:first-child { font-size: 19px; }
  .contacts svg { width: 17px; height: 17px; flex: none; fill: var(--pink); }

  .back-brand {
    position: absolute;
    right: 65px;
    bottom: 44px;
    text-align: left;
    font-family: "Questrial", sans-serif;
    color: var(--white);
    line-height: 1;
  }
  .back-brand .line1 { display: block; font-size: 54px; }
  .back-brand .line2 { display: block; font-size: 32px; margin-top: 6px; margin-left: 3px; }
</style>
</head>
<body>

<section class="card card--front">
  <div class="brand">
    <span class="brand__dot"></span>
    <div class="brand__name">
      <span class="line1">Harborlight</span>
      <span class="line2">Elder Aides</span>
    </div>
  </div>

  <div class="person">
    <div class="person__name">DELIA PARKHURST</div>
    <div class="person__role">Owner</div>
  </div>

  <div class="divider"></div>

  <ul class="contacts">
    <li>
      <svg viewBox="0 0 24 24" aria-hidden="true"><path d="M6.6 10.8a15.2 15.2 0 0 0 6.6 6.6l2.2-2.2a1 1 0 0 1 1-.25 11.4 11.4 0 0 0 3.6.57 1 1 0 0 1 1 1V20a1 1 0 0 1-1 1A17 17 0 0 1 3 4a1 1 0 0 1 1-1h3.5a1 1 0 0 1 1 1c0 1.25.2 2.45.57 3.57a1 1 0 0 1-.25 1z"/></svg>
      936.482.5079
    </li>
    <li>
      <svg viewBox="0 0 24 24" aria-hidden="true"><path d="M2 5h20v14H2z M3.5 6.5 12 12.5l8.5-6z" fill-rule="evenodd"/></svg>
      Delia@harborlightelderaides.com
    </li>
    <li>
      <svg viewBox="0 0 24 24" aria-hidden="true"><path d="M12 2a10 10 0 1 0 0 20 10 10 0 0 0 0-20zm0 2a8 8 0 0 1 6.9 4H15l-1.5 2 1.5 3-2 3v2.9A8 8 0 0 1 4.3 9.5L8 12l1 3 2-1V11L8 9l1-3 3-2z"/></svg>
      HarborlightElderAides.com
    </li>
    <li>
      <svg viewBox="0 0 24 24" aria-hidden="true"><path d="M12 2a7 7 0 0 0-7 7c0 5 7 13 7 13s7-8 7-13a7 7 0 0 0-7-7zm0 4a3 3 0 1 1 0 6 3 3 0 0 1 0-6z" fill-rule="evenodd"/></svg>
      Alder Springs, Texas
    </li>
  </ul>
</section>

<section class="card card--back">
  <div class="back-brand">
    <span class="line1">Harborlight</span>
    <span class="line2">Elder Aides</span>
  </div>
</section>

</body>
</html>
```